Business card for law firm

Need business card for new law firm. Think confident, authoritative, conservative, but not stuffy or old-fashioned.

Contact Information for Business Card

Content for card - logo (uploaded), plus the following:

Paul Whitcombe (larger font)
Managing Partner (larger font, but not as large as name)
Level 9, 7 Ferris Lane
Sydney NSW 2000
Main Tel 02 9364 2710
Direct Tel 02 8472 3159
Email paul@qvlegal.com.au
www.qvlegal.com.au

Letterhead design should include logo plus:
Level 9, 7 Ferris Lane
Sydney NSW 2000
Tel 02 8472 3159
www.qvlegal.com.au

```html
<!DOCTYPE html>
<html lang="en">
<head>
<meta charset="utf-8">
<title>Quayview Legal – Business Card</title>
<link rel="stylesheet" href="https://fonts.googleapis.com/css2?family=Cinzel:wght@600&family=Nunito+Sans:wght@400&display=swap">
<style>
  :root {
    --backdrop: #ebe6de;
    --navy-light: #2c3a78;
    --navy-deep: #18214d;
    --gold: #d8c9a4;
    --gold-soft: #cbbd99;
  }
  html, body {
    margin: 0;
    width: 1200px;
    height: 1047px;
    overflow: hidden;
    background: var(--backdrop);
  }
  .canvas {
    position: relative;
    width: 1200px;
    height: 1047px;
  }
  .business-card {
    position: absolute;
    left: 151px;
    top: 292px;
    width: 945px;
    height: 513px;
    filter: drop-shadow(0 10px 24px rgba(20, 25, 50, 0.22));
  }
  .card-base { fill: url(#navyGradient); }
  .person-name {
    font-family: "Cinzel", serif;
    font-weight: 600;
    font-size: 27px;
    fill: var(--gold);
  }
  .person-title,
  .contact-line,
  .address-line {
    font-family: "Nunito Sans", sans-serif;
    font-size: 19px;
    fill: var(--gold);
  }
  .website {
    font-family: "Nunito Sans", sans-serif;
    font-size: 18px;
    letter-spacing: 1.6px;
    fill: var(--gold-soft);
  }
  .contact-icon {
    fill: none;
    stroke: var(--gold);
    stroke-width: 1.6;
    stroke-linejoin: round;
    stroke-linecap: round;
  }
  .contact-icon.solid { fill: var(--gold); stroke: none; }
  .brand-square { fill: var(--gold); }
  .brand-name {
    font-family: "Nunito Sans", sans-serif;
    font-weight: 400;
    font-size: 30px;
    fill: var(--gold);
  }
</style>
</head>
<body>
<main class="canvas">
  <svg class="business-card" viewBox="0 0 875 475" xmlns="http://www.w3.org/2000/svg" aria-label="Business card for Paul Whitcombe, Quayview Legal">
    <defs>
      <linearGradient id="navyGradient" x1="0" y1="0" x2="1" y2="1">
        <stop offset="0" stop-color="var(--navy-light)"/>
        <stop offset="1" stop-color="var(--navy-deep)"/>
      </linearGradient>
    </defs>

    <rect class="card-base" width="875" height="475" rx="18"/>

    <text class="person-name" x="40" y="93">PAUL WHITCOMBE</text>
    <text class="person-title" x="40" y="122">Managing Partner</text>

    <g class="contact-details">
      <path class="contact-icon solid" d="M42 251 c0-2 2-3 3-3 l2 0 2 5 -2 2 c1 2 3 4 5 5 l2-2 5 2 0 2 c0 1-1 3-3 3 c-8 0-14-6-14-14z"/>
      <text class="contact-line" x="68" y="265">02 9364 2710</text>

      <rect class="contact-icon" x="43" y="277" width="9" height="15" rx="1.8"/>
      <text class="contact-line" x="68" y="293">02 8472 3159</text>

      <rect class="contact-icon" x="40" y="310" width="15" height="10" rx="1"/>
      <path class="contact-icon" d="M40 311 l7.5 5.5 7.5-5.5"/>
      <text class="contact-line" x="68" y="322">paul@qvlegal.com.au</text>
    </g>

    <g class="address">
      <text class="address-line" x="37" y="368">Level 9, 7 Ferris Lane</text>
      <text class="address-line" x="37" y="396">Sydney NSW 2000</text>
    </g>

    <text class="website" x="37" y="441">www.qvlegal.com.au</text>

    <g class="brand">
      <rect class="brand-square" x="566" y="226" width="22" height="22"/>
      <text class="brand-name" x="600" y="247">Quayview Legal</text>
    </g>
  </svg>
</main>
</body>
</html>
```